Calden L - Premium Business Cards

Background of Calden L
Calden Leafworks is a cigar mobile lounge where guests become family. A place of luxury, relaxation, and ambiance is the global popularity demand. Calden Leafworks strives to provide first-class service of quality and products. Our goal is to ensure that every guest is treated and serviced as a VIP.

Calden Leafworks was founded by Dennis Markow Jr in January 2020. After 15 years of cigar reviews and research Dennis decided it was time to launch his own cigar brand and boutique cigar company. With a wealth of knowledge and years of experience Calden Leafworks was born. With opulence for all cultures, Calden Leafworks offers hand rolled cigars with premium blend tobacco from sweet to bold imported from Costa Rica, Dominican Republic, and Nicaragua. Thank you for your business!

Objective:
Create a business card template to be used for all employees. Design should communicate premium and classy. And should use earth tone colors.

Design should include:
1. Client wants to incorporate the cigar leaf
2. Logo
3. Tagline: Savor every leaf
3. Content info:
Kevin Oldacre
Owner
555-017-4863
koldacre@caldenleaf.com
caldenleafworks.com

```html
<!DOCTYPE html>
<html lang="en">
<head>
<meta charset="utf-8">
<title>Calden Leafworks – Business Cards</title>
<link rel="stylesheet" href="https://fonts.googleapis.com/css2?family=Poppins:wght@300;400;600;700&display=swap">
<style>
  :root {
    --page-bg: #1c1b1f;
    --card-bg: #262629;
    --card-edge: #303034;
    --ink: #f2f2f2;
    --ink-soft: #c9c9cc;
    --rule: #9a9a9e;
    --smoke-dark: #141416;
    --smoke-mid: #1f1f22;
  }
  * { box-sizing: border-box; margin: 0; padding: 0; }
  html, body { width: 1200px; height: 800px; overflow: hidden; }
  body {
    background: var(--page-bg);
    font-family: "Poppins", sans-serif;
    color: var(--ink);
    display: flex;
    align-items: center;
    justify-content: center;
    gap: 40px;
  }
  .card {
    position: relative;
    width: 520px;
    height: 298px;
    background: var(--card-bg);
    border: 1px solid var(--card-edge);
    border-radius: 22px;
    overflow: hidden;
    box-shadow: 0 18px 40px rgba(0,0,0,.45);
  }
  .brand-name {
    font-family: "Poppins", sans-serif;
    font-weight: 700;
    color: var(--ink);
    text-transform: uppercase;
    line-height: 1.05;
    letter-spacing: 1px;
  }
  .rule-line {
    position: absolute;
    height: 1px;
    background: var(--rule);
  }
  .rule-line::before, .rule-line::after {
    content: "";
    position: absolute;
    top: -2px;
    width: 5px; height: 5px;
    border-radius: 50%;
    background: var(--ink-soft);
  }
  .rule-line::before { left: -2px; }
  .rule-line::after { right: -2px; }

  /* Front */
  .card-front .brand-block {
    position: absolute;
    left: 0; right: 0; top: 92px;
    text-align: center;
  }
  .card-front .brand-name { font-size: 36px; }
  .card-front .rule-top { top: 80px; left: 330px; width: 80px; }
  .card-front .rule-bottom { top: 190px; left: 110px; width: 80px; }
  .tagline {
    position: absolute;
    left: 0; right: 0; top: 204px;
    text-align: center;
    font-size: 12px;
    font-weight: 400;
    letter-spacing: 7px;
    color: var(--ink-soft);
    text-transform: uppercase;
  }

  /* Back */
  .card-back .smoke-area {
    position: absolute;
    right: 0; bottom: 0;
    width: 330px; height: 180px;
  }
  .card-back .brand-block {
    position: absolute;
    left: 34px; top: 120px;
    width: 200px;
  }
  .card-back .brand-name { font-size: 26px; }
  .card-back .rule-top { top: 108px; left: 150px; width: 70px; }
  .card-back .rule-bottom { top: 196px; left: 34px; width: 70px; }
  .divider {
    position: absolute;
    left: 252px; top: 56px;
    width: 1px; height: 150px;
    background: var(--rule);
  }
  .divider::before, .divider::after {
    content: "";
    position: absolute;
    left: -2px;
    width: 5px; height: 5px;
    border-radius: 50%;
    background: var(--ink-soft);
  }
  .divider::before { top: -2px; }
  .divider::after { bottom: -2px; }
  .contact {
    position: absolute;
    left: 272px; top: 58px;
  }
  .contact-name {
    font-size: 17px;
    font-weight: 700;
    text-transform: uppercase;
    letter-spacing: .5px;
  }
  .contact-role {
    font-size: 12px;
    font-weight: 300;
    color: var(--ink-soft);
    margin-bottom: 16px;
  }
  .contact-list { list-style: none; }
  .contact-list li {
    display: flex;
    align-items: center;
    gap: 8px;
    font-size: 12px;
    font-weight: 400;
    line-height: 22px;
  }
  .contact-list svg { width: 13px; height: 13px; flex: none; }
</style>
</head>
<body>

  <section class="card card-front" aria-label="Business card front">
    <span class="rule-line rule-top"></span>
    <div class="brand-block">
      <p class="brand-name">Calden Leafworks</p>
    </div>
    <span class="rule-line rule-bottom"></span>
    <p class="tagline">Savor every leaf</p>
  </section>

  <section class="card card-back" aria-label="Business card back">
    <svg class="smoke-area" viewBox="0 0 330 180" role="img" aria-label="Flowing cigar smoke decoration in dark tones">
      <defs>
        <linearGradient id="smokeFade" x1="0" y1="1" x2="1" y2="0">
          <stop offset="0" stop-color="var(--smoke-mid)" stop-opacity="0"/>
          <stop offset=".5" stop-color="var(--smoke-mid)"/>
          <stop offset="1" stop-color="var(--smoke-dark)"/>
        </linearGradient>
      </defs>
      <path d="M0 180 C90 150 150 120 200 60 C240 20 290 10 330 8 L330 180 Z" fill="url(#smokeFade)"/>
    </svg>

    <span class="rule-line rule-top"></span>
    <div class="brand-block">
      <p class="brand-name">Calden<br>Leafworks</p>
    </div>
    <span class="rule-line rule-bottom"></span>

    <span class="divider"></span>

    <div class="contact">
      <p class="contact-name">Kevin Oldacre</p>
      <p class="contact-role">Owner</p>
      <ul class="contact-list">
        <li>
          <svg viewBox="0 0 24 24" aria-hidden="true"><path fill="#f2f2f2" d="M6.6 10.8a15 15 0 0 0 6.6 6.6l2.2-2.2c.3-.3.7-.4 1-.2 1.1.4 2.3.6 3.6.6.6 0 1 .4 1 1V20c0 .6-.4 1-1 1C10.6 21 3 13.4 3 4c0-.6.4-1 1-1h3.5c.6 0 1 .4 1 1 0 1.3.2 2.5.6 3.6.1.3 0 .7-.2 1z"/></svg>
          555-017-4863
        </li>
        <li>
          <svg viewBox="0 0 24 24" aria-hidden="true"><path fill="#f2f2f2" d="M2 5h20v14H2z"/><path fill="none" stroke="#262629" stroke-width="1.6" d="M2.5 5.5 12 13l9.5-7.5"/></svg>
          koldacre@caldenleaf.com
        </li>
        <li>
          <svg viewBox="0 0 24 24" aria-hidden="true"><circle cx="12" cy="12" r="10" fill="#f2f2f2"/><path fill="none" stroke="#262629" stroke-width="1.3" d="M2 12h20M12 2c3 3 3 17 0 20M12 2c-3 3-3 17 0 20"/></svg>
          caldenleafworks.com
        </li>
      </ul>
    </div>
  </section>

</body>
</html>
```